Premium Photoshop/Illustrator Template for Adventure Map Prints

Premium Adventure Print Template for VELOK Odyssey
About the Project
I am launching a business called VELOK Odyssey.
Customers send me a GPS track (GPX file) from an adventure they have completed, such as:
Trail running
Hiking
Mountain biking
Ski touring
Road cycling
Mountain ascents
Adventure racing
I create a high-quality map using professional GIS software and produce a premium wall print that commemorates their adventure.
This is not a one-off poster design.
I need a reusable Photoshop template that I can use for hundreds of different adventures by simply replacing the map, statistics and adventure information.
Design Style
I am looking for a design that feels:
Premium
Modern
Minimal
Clean
Sophisticated
Timeless
The finished product should look like something people would proudly frame and display in their home.
I like the clean, premium aesthetic of brands such as Kolvex, MIRAN, Pellva, Bruneo and FenWander.
I prefer subtle, elegant design rather than something busy or cluttered.
The map should always be the hero of the design.
This should feel like premium wall art rather than a dashboard of statistics. The information should enhance the story of the adventure without competing with the map for attention.
Template Requirements
The Photoshop template should include editable placeholders for:
Adventure title
Athlete name
Date
Main map
Adventure statistics
Elevation profile
Optional race or event photo
Optional event logo
VELOK Odyssey logo
Website address
Optional location icon or subtle design elements
The map and elevation profile will be created by me using professional GIS software and inserted into the template.
The designer does not need to create these graphics.
Layout Preference
My preferred direction is for the map to extend to the edges of the print wherever possible, with the information presented as subtle floating panels over the map rather than within a large fixed sidebar.
The map should occupy as much of the page as possible and remain the primary visual focus.
The main information panel should be compact and elegant, allowing the artwork to dominate the composition rather than the information.
The layout should feel balanced, modern and premium while remaining practical to update for hundreds of different adventures.
Flexibility
The template needs to work with adventures of many different shapes and sizes.
Some routes are short loops.
Others may be over 100 km long.
The layout should work equally well in both portrait and landscape orientations and should scale naturally from A3 through to A0 without requiring the design to be recreated.
The template should also work equally well for trail running, hiking, mountain biking, road cycling, ski touring and other adventure sports.
Modular Layout
This template will become a reusable design system rather than a single fixed poster layout.
I would like the template to consist of several logical grouped elements that can easily be updated for each new adventure.
Main Information Panel
The following elements should form one grouped panel:
Adventure title
Athlete name
Date
Adventure statistics
Optional Kolvex-inspired metric dial
VELOK Odyssey logo
Website address
This grouped panel should be easy to resize and reposition if required so that it works with different map layouts, route shapes and print sizes.
The information panel should remain subtle and elegant. It should support the map rather than dominate it.
The VELOK Odyssey logo should be used as discreet branding rather than the main visual focus.
Typical statistics may include:
Distance
Elevation gain
Moving time
Average pace or average speed
Maximum elevation
Date
Additional metrics may be displayed depending on the activity.
Elevation Profile
The elevation profile should be a separate replaceable placeholder that can easily be updated for each new adventure without recreating the design.
It should also be able to be repositioned or resized if required to best suit the overall composition.
Optional Photo / Event Panel
Please include a separate optional placeholder for a race photo, event logo or similar content.
This element should be able to be shown or hidden while the overall layout still feels balanced and intentional.
Speed/Pace Legend
Please include an optional placeholder for the route colour legend. This should be designed as a separate element that can be shown, hidden or repositioned depending on the adventure while maintaining a clean, balanced layout.
Deliverables
Please supply:
Fully layered Photoshop (.PSD) files
Landscape template (A3)
Portrait template (A3)
Both templates should use the same design language and branding
Clearly organised layer groups
Editable text layers
Smart Objects or an equally simple method for replacing the map, elevation profile and optional images
Locked design elements where appropriate
Print-ready at 300 dpi
The templates should be quick and intuitive to update for each new adventure.
The templates should also be designed so they can be easily adapted to A2, A1 and A0 print sizes without requiring the layout to be redesigned.
Source Files
Please provide:
Layered Photoshop (.PSD) files
Any Illustrator (.AI) files used during the design process
Names of all fonts used (preferably Adobe Fonts where possible)
Any graphics or assets used within the design
Files Provided
I have attached:
My current draft design
The VELOK Odyssey logo
Sample map artwork
A Kolvex watch face for design inspiration
These are intended to demonstrate the concept only.
I am looking for a designer to create a much more polished, modern and premium version of this product.
Creative Direction
Please don't feel constrained by my existing layout. The attached design is simply to demonstrate the concept and the information that needs to be included.
I welcome fresh, creative ideas and different layouts, provided the design remains clean, premium and the map remains the hero of the print.
I particularly like the clean design language and circular metric dial shown on the Kolvex watch face. I would like this to be explored as an optional design element, but not copied directly.
I also like the idea of incorporating a very subtle contour or topographic line texture into the information panels or backgrounds to reinforce the outdoor and mapping theme. This should remain understated and elegant so it adds depth without distracting from the map.
The finished template should establish a distinctive visual identity that can be used consistently across the VELOK Odyssey product range.
When someone receives one of these prints, I want their first reaction to be "Wow." It should celebrate the adventure, tell the story of the journey and become something they are proud to frame and display in their home.
Update - I have attached a couple of files that I would like to explore incorporating into the background of my information boxes, maybe just a subtle contour texture, similar to the watch face attached.
Workflow clarification: This template will be used to produce many posters. For each order, I'll be replacing the map, GPX route and statistics with new content exported from QGIS. My priority is an efficient workflow that allows me to update these elements quickly while maintaining a high-quality design. I'm happy for the master template to be created in Illustrator if that's the best approach, with Photoshop used where appropriate for image editing. Please keep this workflow in mind when designing the template and let me know if you have any recommendations.

```html
<!DOCTYPE html>
<html lang="en">
<head>
<meta charset="utf-8">
<title>VELOK Odyssey – Info Panel Ideas</title>
<link rel="stylesheet" href="https://fonts.googleapis.com/css2?family=Inter:wght@300;400;500;700&display=swap">
<style>
  :root{
    --sheet:#ffffff;
    --label:#1a1a1a;
    --panel:#333e3f;
    --panel-deep:#1c292c;
    --panel-edge:#27312f;
    --text:#f1f3f1;
    --muted:#c9cfcc;
    --accent:#f29a1f;
    --rule:rgba(255,255,255,.12);
    --brand:#b9bfbd;
    --red:#ef4b2f;
    --orange:#f7931e;
    --yellow:#e4e52a;
    --green:#4fc85a;
    --blue:#2ec2ee;
  }
  *{box-sizing:border-box;margin:0;padding:0}
  html,body{width:1200px;height:670px;overflow:hidden;background:var(--sheet)}
  body{position:relative;font-family:"Inter",Arial,sans-serif;color:var(--text)}

  .idea-label{position:absolute;width:250px;text-align:center;font-size:12px;color:var(--label);font-weight:400}
  .row-1 .idea-label{top:17px}
  .row-2 .idea-label{top:316px}

  .panel{position:absolute;width:250px;height:258px;border-radius:7px;overflow:hidden;border:1px solid var(--panel-edge)}
  .row-1 .panel{top:40px}
  .row-2 .panel{top:345px}
  .col-1{left:41px}.col-2{left:303px}.col-3{left:570px}.col-4{left:837px}

  .topo{position:absolute;inset:0;background:radial-gradient(ellipse at 70% 35%,#3d494a 0%,var(--panel) 55%,#2c3637 100%)}
  .topo.deep{background:radial-gradient(ellipse at 70% 35%,#243437 0%,var(--panel-deep) 60%,#172326 100%)}
  .topo.strong{background:radial-gradient(ellipse at 25% 20%,#3a4647 0%,#2a3435 40%,#364243 65%,#263031 100%)}

  .content{position:absolute;inset:0}
  .title{position:absolute;left:14px;top:14px;font-size:17.9px;font-weight:700;letter-spacing:-.2px;white-space:nowrap;line-height:1.1}
  .route{position:absolute;left:14px;top:35px;font-size:5.4px;font-weight:500;letter-spacing:1px;color:var(--accent);white-space:nowrap}
  .athlete{position:absolute;left:14px;top:53px;font-size:5.8px;font-weight:500;letter-spacing:1px}
  .date{position:absolute;left:14px;top:62px;font-size:5.2px;letter-spacing:.6px;color:var(--muted)}
  .rule{position:absolute;left:14px;right:14px;height:1px;background:var(--rule)}
  .rule.top{top:76px}.rule.bottom{top:197px}

  .stat{position:absolute;padding-left:6px;border-left:1.5px solid var(--c)}
  .stat .k{display:block;font-size:4.8px;letter-spacing:.9px;color:var(--muted);line-height:1}
  .stat .v{display:block;font-size:10.4px;font-weight:400;margin-top:3px;line-height:1;white-space:nowrap}
  .s-elev{left:14px;top:89px;--c:var(--orange)}
  .s-pace{left:90px;top:89px;--c:var(--green)}
  .s-time{left:14px;top:118px;--c:var(--yellow)}
  .s-max{left:90px;top:118px;--c:var(--blue)}

  .info{position:absolute}
  .info .k{display:block;font-size:4.8px;letter-spacing:.9px;color:var(--muted);line-height:1}
  .info .v{display:block;font-size:8px;margin-top:4px;line-height:1;white-space:nowrap}
  .i-activity{left:14px;top:156px}
  .i-location{left:90px;top:156px}

  .dial{position:absolute;left:158px;top:83px;width:64px;height:64px}
  .dial-value{position:absolute;left:158px;top:106px;width:64px;text-align:center;font-size:17px;font-weight:300;line-height:1}
  .dial-unit{position:absolute;left:158px;top:126px;width:64px;text-align:center;font-size:4.4px;letter-spacing:1px;font-weight:500}

  .brand{position:absolute;left:10px;top:235px}
  .brand-name{display:block;font-size:8px;font-weight:700;color:var(--brand);letter-spacing:.2px;line-height:1}
  .brand-tag{display:block;font-size:3.6px;color:var(--brand);margin-top:1px;line-height:1}
  .site{position:absolute;right:15px;top:241px;font-size:5.4px;color:var(--text);line-height:1}
</style>
</head>
<body>

<svg width="0" height="0" style="position:absolute" aria-hidden="true">
  <defs>
    <g id="gauge" fill="none" stroke-width="4" stroke-linecap="round">
      <circle cx="32" cy="32" r="24" fill="rgba(0,0,0,.18)" stroke="none"/>
      <path d="M12.2 51.8 A28 28 0 0 1 4.1 34.4" stroke="var(--red)"/>
      <path d="M4 31 A28 28 0 0 1 14 10.6" stroke="var(--orange)"/>
      <path d="M18 7.8 A28 28 0 0 1 46 7.8" stroke="var(--yellow)"/>
      <path d="M50 10.6 A28 28 0 0 1 60 31" stroke="var(--green)"/>
      <path d="M59.9 34.4 A28 28 0 0 1 51.8 51.8" stroke="var(--blue)"/>
      <g stroke="rgba(255,255,255,.35)" stroke-width=".6">
        <line x1="32" y1="10" x2="32" y2="12"/>
        <line x1="10" y1="32" x2="12" y2="32"/>
        <line x1="54" y1="32" x2="52" y2="32"/>
      </g>
    </g>
  </defs>
</svg>

<section class="row-1">
  <div class="idea-label col-1">Idea #001</div>
  <article class="panel col-1">
    <div class="topo" role="img" aria-label="Subtle topographic contour texture"></div>
    <div class="content">
      <h1 class="title">ALPINE RIDGE TRAVERSE</h1>
      <p class="route">15 KM | TARVEN DOZER LINE</p>
      <p class="athlete">JONAH KELLER</p><p class="date">12 OCTOBER 2025</p>
      <div class="rule top"></div>
      <div class="stat s-elev"><span class="k">ELEVATION GAIN</span><span class="v">3,842 M</span></div>
      <div class="stat s-pace"><span class="k">AVG. PACE</span><span class="v">6:46 /KM</span></div>
      <div class="stat s-time"><span class="k">MOVING TIME</span><span class="v">11:47:32</span></div>
      <div class="stat s-max"><span class="k">MAX ELEVATION</span><span class="v">1,742 M</span></div>
      <svg class="dial" viewBox="0 0 64 64"><use href="#gauge"/></svg>
      <div class="dial-value">104.6</div><div class="dial-unit">KM</div>
      <div class="info i-activity"><span class="k">ACTIVITY</span><span class="v">TRAIL RUNNING</span></div>
      <div class="info i-location"><span class="k">LOCATION</span><span class="v">ALPINE RIDGE</span></div>
      <div class="rule bottom"></div>
      <div class="brand"><span class="brand-name">VELOK ODYSSEY</span><span class="brand-tag">every route, remembered</span></div>
      <div class="site">velokodyssey.com</div>
    </div>
  </article>

  <div class="idea-label col-2">Idea #002</div>
  <article class="panel col-2">
    <div class="topo" role="img" aria-label="Subtle topographic contour texture"></div>
    <div class="content">
      <h1 class="title">ALPINE RIDGE TRAVERSE</h1>
      <p class="route">15 KM | TARVEN DOZER LINE</p>
      <p class="athlete">JONAH KELLER</p><p class="date">12 OCTOBER 2025</p>
      <div class="rule top"></div>
      <div class="stat s-elev"><span class="k">ELEVATION GAIN</span><span class="v">3,842 M</span></div>
      <div class="stat s-pace"><span class="k">AVG. PACE</span><span class="v">6:46 /KM</span></div>
      <div class="stat s-time"><span class="k">MOVING TIME</span><span class="v">11:47:32</span></div>
      <div class="stat s-max"><span class="k">MAX ELEVATION</span><span class="v">1,742 M</span></div>
      <svg class="dial" viewBox="0 0 64 64"><use href="#gauge"/></svg>
      <div class="dial-value">104.6</div><div class="dial-unit">KM</div>
      <div class="info i-activity"><span class="k">ACTIVITY</span><span class="v">TRAIL RUNNING</span></div>
      <div class="info i-location"><span class="k">LOCATION</span><span class="v">ALPINE RIDGE</span></div>
      <div class="rule bottom"></div>
      <div class="brand"><span class="brand-name">VELOK ODYSSEY</span><span class="brand-tag">every route, remembered</span></div>
      <div class="site">velokodyssey.com</div>
    </div>
  </article>

  <div class="idea-label col-3">Idea #003</div>
  <article class="panel col-3">
    <div class="topo" role="img" aria-label="Subtle topographic contour texture"></div>
    <div class="content">
      <h1 class="title">ALPINE RIDGE TRAVERSE</h1>
      <p class="route">15 KM | TARVEN DOZER LINE</p>
      <p class="athlete">JONAH KELLER</p><p class="date">12 OCTOBER 2025</p>
      <div class="rule top"></div>
      <div class="stat s-elev"><span class="k">ELEVATION GAIN</span><span class="v">3,842 M</span></div>
      <div class="stat s-pace"><span class="k">AVG. PACE</span><span class="v">6:46 /KM</span></div>
      <div class="stat s-time"><span class="k">MOVING TIME</span><span class="v">11:47:32</span></div>
      <div class="stat s-max"><span class="k">MAX ELEVATION</span><span class="v">1,742 M</span></div>
      <svg class="dial" viewBox="0 0 64 64"><use href="#gauge"/></svg>
      <div class="dial-value">104.6</div><div class="dial-unit">KM</div>
      <div class="info i-activity"><span class="k">ACTIVITY</span><span class="v">TRAIL RUNNING</span></div>
      <div class="info i-location"><span class="k">LOCATION</span><span class="v">ALPINE RIDGE</span></div>
      <div class="rule bottom"></div>
      <div class="brand"><span class="brand-name">VELOK ODYSSEY</span><span class="brand-tag">every route, remembered</span></div>
      <div class="site">velokodyssey.com</div>
    </div>
  </article>

  <div class="idea-label col-4">Idea #004</div>
  <article class="panel col-4">
    <div class="topo deep" role="img" aria-label="Subtle topographic contour texture in deep teal"></div>
    <div class="content">
      <h1 class="title">ALPINE RIDGE TRAVERSE</h1>
      <p class="route">15 KM | TARVEN DOZER LINE</p>
      <p class="athlete">JONAH KELLER</p><p class="date">12 OCTOBER 2025</p>
      <div class="rule top"></div>
      <div class="stat s-elev"><span class="k">ELEVATION GAIN</span><span class="v">3,842 M</span></div>
      <div class="stat s-pace"><span class="k">AVG. PACE</span><span class="v">6:46 /KM</span></div>
      <div class="stat s-time"><span class="k">MOVING TIME</span><span class="v">11:47:32</span></div>
      <div class="stat s-max"><span class="k">MAX ELEVATION</span><span class="v">1,742 M</span></div>
      <svg class="dial" viewBox="0 0 64 64"><use href="#gauge"/></svg>
      <div class="dial-value">104.6</div><div class="dial-unit">KM</div>
      <div class="info i-activity"><span class="k">ACTIVITY</span><span class="v">TRAIL RUNNING</span></div>
      <div class="info i-location"><span class="k">LOCATION</span><span class="v">ALPINE RIDGE</span></div>
      <div class="rule bottom"></div>
      <div class="brand"><span class="brand-name">VELOK ODYSSEY</span><span class="brand-tag">every route, remembered</span></div>
      <div class="site">velokodyssey.com</div>
    </div>
  </article>
</section>

<section class="row-2">
  <div class="idea-label col-1">Idea #005</div>
  <article class="panel col-1">
    <div class="topo strong" role="img" aria-label="Layered topographic contour relief texture"></div>
    <div class="content">
      <h1 class="title">ALPINE RIDGE TRAVERSE</h1>
      <p class="route">15 KM | TARVEN DOZER LINE</p>
      <p class="athlete">JONAH KELLER</p><p class="date">12 OCTOBER 2025</p>
      <div class="stat s-elev"><span class="k">ELEVATION GAIN</span><span class="v">3,842 M</span></div>
      <div class="stat s-pace"><span class="k">AVG. PACE</span><span class="v">6:46 /KM</span></div>
      <div class="stat s-time"><span class="k">MOVING TIME</span><span class="v">11:47:32</span></div>
      <div class="stat s-max"><span class="k">MAX ELEVATION</span><span class="v">1,742 M</span></div>
      <svg class="dial" viewBox="0 0 64 64"><use href="#gauge"/></svg>
      <div class="dial-value">104.6</div><div class="dial-unit">KM</div>
      <div class="info i-activity"><span class="k">ACTIVITY</span><span class="v">TRAIL RUNNING</span></div>
      <div class="info i-location"><span class="k">LOCATION</span><span class="v">ALPINE RIDGE</span></div>
      <div class="rule bottom"></div>
      <div class="brand"><span class="brand-name">VELOK ODYSSEY</span><span class="brand-tag">every route, remembered</span></div>
      <div class="site">velokodyssey.com</div>
    </div>
  </article>

  <div class="idea-label col-2">Idea #006</div>
  <article class="panel col-2">
    <div class="topo strong" role="img" aria-label="Layered topographic contour relief texture"></div>
    <div class="content">
      <h1 class="title">ALPINE RIDGE TRAVERSE</h1>
      <p class="route">15 KM | TARVEN DOZER LINE</p>
      <p class="athlete">JONAH KELLER</p><p class="date">12 OCTOBER 2025</p>
      <div class="stat s-elev"><span class="k">ELEVATION GAIN</span><span class="v">3,842 M</span></div>
      <div class="stat s-pace"><span class="k">AVG. PACE</span><span class="v">6:46 /KM</span></div>
      <div class="stat s-time"><span class="k">MOVING TIME</span><span class="v">11:47:32</span></div>
      <div class="stat s-max"><span class="k">MAX ELEVATION</span><span class="v">1,742 M</span></div>
      <svg class="dial" viewBox="0 0 64 64"><use href="#gauge"/></svg>
      <div class="dial-value">104.6</div><div class="dial-unit">KM</div>
      <div class="info i-activity"><span class="k">ACTIVITY</span><span class="v">TRAIL RUNNING</span></div>
      <div class="info i-location"><span class="k">LOCATION</span><span class="v">ALPINE RIDGE</span></div>
      <div class="rule bottom"></div>
      <div class="brand"><span class="brand-name">VELOK ODYSSEY</span><span class="brand-tag">every route, remembered</span></div>
      <div class="site">velokodyssey.com</div>
    </div>
  </article>

  <div class="idea-label col-3">Idea #007</div>
  <article class="panel col-3">
    <div class="topo" role="img" aria-label="Subtle topographic contour texture"></div>
    <div class="content">
      <h1 class="title">ALPINE RIDGE TRAVERSE</h1>
      <p class="route">15 KM | TARVEN DOZER LINE</p>
      <p class="athlete">JONAH KELLER</p><p class="date">12 OCTOBER 2025</p>
      <div class="stat s-elev"><span class="k">ELEVATION GAIN</span><span class="v">3,842 M</span></div>
      <div class="stat s-pace"><span class="k">AVG. PACE</span><span class="v">6:46 /KM</span></div>
      <div class="stat s-time"><span class="k">MOVING TIME</span><span class="v">11:47:32</span></div>
      <div class="stat s-max"><span class="k">MAX ELEVATION</span><span class="v">1,742 M</span></div>
      <svg class="dial" viewBox="0 0 64 64"><use href="#gauge"/></svg>
      <div class="dial-value">104.6</div><div class="dial-unit">KM</div>
      <div class="info i-activity"><span class="k">ACTIVITY</span><span class="v">TRAIL RUNNING</span></div>
      <div class="info i-location"><span class="k">LOCATION</span><span class="v">ALPINE RIDGE</span></div>
      <div class="rule bottom"></div>
      <div class="brand"><span class="brand-name">VELOK ODYSSEY</span><span class="brand-tag">every route, remembered</span></div>
      <div class="site">velokodyssey.com</div>
    </div>
  </article>

  <div class="idea-label col-4">Idea #008</div>
  <article class="panel col-4">
    <div class="topo strong" role="img" aria-label="Bold layered topographic contour relief texture"></div>
    <div class="content">
      <h1 class="title">ALPINE RIDGE TRAVERSE</h1>
      <p class="route">15 KM | TARVEN DOZER LINE</p>
      <p class="athlete">JONAH KELLER</p><p class="date">12 OCTOBER 2025</p>
      <div class="stat s-elev"><span class="k">ELEVATION GAIN</span><span class="v">3,842 M</span></div>
      <div class="stat s-pace"><span class="k">AVG. PACE</span><span class="v">6:46 /KM</span></div>
      <div class="stat s-time"><span class="k">MOVING TIME</span><span class="v">11:47:32</span></div>
      <div class="stat s-max"><span class="k">MAX ELEVATION</span><span class="v">1,742 M</span></div>
      <svg class="dial" viewBox="0 0 64 64"><use href="#gauge"/></svg>
      <div class="dial-value">104.6</div><div class="dial-unit">KM</div>
      <div class="info i-activity"><span class="k">ACTIVITY</span><span class="v">TRAIL RUNNING</span></div>
      <div class="info i-location"><span class="k">LOCATION</span><span class="v">ALPINE RIDGE</span></div>
      <div class="brand"><span class="brand-name">VELOK ODYSSEY</span><span class="brand-tag">every route, remembered</span></div>
      <div class="site">velokodyssey.com</div>
    </div>
  </article>
</section>

</body>
</html>
```